Business Cards for new orthopaedic surgery practice

My husband and I are starting our own orthopaedic surgery practice. We are looking for a business card that is uniform, but one will have my name/title and the other will have his. You can just create one design with my name on it for now. But when I choose your design as the winning design I will ask that you add another copy with his name/title.

We are looking for classy, simple, elite all in one. We like dark blues/a little gold/yellow. Something that goes with our logo. We want our logo incorporated. Here is all the info you need:
Business name: RV Bone & Vitality Center
Location: 38517 North Willowmere Ave
Maple Harbor, FL 33098
Phone: 954-218-4063
Fax: 954-582-7341
Email: info@myrvbonecare.example

Names: Lydia Vance, M.D.
Board Certified Hand and Upper Extremity Surgeon

Ebo Dansu, M.D.
Board Certified Hip & Knee Replacement/General Orthopaedic Surgeon

Can decide what you want to put on the back. Maybe a slogan:
Rooted in Care. Focused on You

I am just going to upload our logo. The only thing is if we select you as the winning design, the location, and phone numbers may change. We will need your help to update that once fully solidified.

Industry/Entity Type

Medical

Contact Information for Business Card

Colors
0054AA
0677BA
7BADD7
CADEEF
E8F1F8
0094D4
00A9DD
6FCCEA
C7EBF8
E9F6FB

Requirements
Must have
• class, appeal,
Should not have
• We want to air on the side of masculine if we are looking at masculine vs. feminine feel. But we still want it classy, sophisticated, and something we will love

```html
<!DOCTYPE html>
<html lang="en">
<head>
<meta charset="utf-8">
<title>RV Bone &amp; Vitality Center – Business Card</title>
<link href="https://fonts.googleapis.com/css2?family=Marcellus&family=Noto+Serif:wght@400;700&display=swap" rel="stylesheet">
<style>
  :root {
    --navy: #27407f;
    --cyan: #1cb5e0;
    --paper: #ffffff;
    --backdrop: #f1f1f1;
    --ink: #2b3f7e;
  }
  * { margin: 0; padding: 0; box-sizing: border-box; }
  html, body { width: 1200px; height: 990px; overflow: hidden; background: var(--backdrop); }
  .stage { position: relative; width: 1200px; height: 990px; }

  .card {
    position: absolute; left: 244px; width: 712px; height: 406px;
    border-left: 5px solid var(--cyan);
    border-bottom: 4px solid var(--cyan);
    box-shadow: 6px 14px 28px rgba(0,0,0,.28);
    overflow: hidden;
  }
  .card--front { top: 68px; background: var(--navy); }
  .card--back { top: 516px; background: var(--paper); }

  .front-name {
    position: absolute; left: 0; right: 0; top: 220px;
    text-align: center; color: #ffffff;
    font-family: "Marcellus", serif; font-size: 37px; line-height: 46px;
    letter-spacing: .5px; text-transform: uppercase; white-space: nowrap;
  }
  .front-sub {
    position: absolute; left: 0; right: 0; top: 262px;
    display: flex; justify-content: center; align-items: center; gap: 14px;
    color: #ffffff; font-family: "Marcellus", serif; font-size: 24px;
    letter-spacing: 2.5px; text-transform: uppercase; line-height: 30px;
  }
  .front-sub__rule { width: 73px; height: 2px; background: #ffffff; }

  .back-name {
    position: absolute; left: 30px; top: 180px; width: 300px;
    color: var(--navy);
    font-family: "Marcellus", serif; font-size: 22px; line-height: 23px;
    text-transform: uppercase;
  }

  .divider {
    position: absolute; left: 351px; top: 81px; width: 1px; height: 244px;
    background: var(--cyan);
  }

  .contact {
    position: absolute; left: 417px; top: 93px; width: 290px;
    font-family: "Noto Serif", serif; color: var(--ink);
  }
  .contact__name {
    color: var(--cyan); font-weight: 700; font-size: 22px;
    letter-spacing: 1.4px; line-height: 1.1; margin-bottom: 4px;
  }
  .contact__title, .contact__address {
    font-size: 14px; line-height: 20.5px; letter-spacing: .4px;
  }
  .contact__address { margin-top: 12px; }
  .contact__list { list-style: none; margin-top: 16px; }
  .contact__list li {
    display: flex; align-items: center; gap: 9px;
    font-size: 14.5px; line-height: 20.5px; letter-spacing: .4px;
    margin-left: -1px;
  }
  .contact__list svg { width: 14px; height: 14px; flex: none; }

  .slogan {
    position: absolute; left: 0; right: 0; top: 357px;
    text-align: center; font-family: "Noto Serif", serif;
    font-size: 16px; color: var(--ink); letter-spacing: .3px;
  }
  .slogan span::before {
    content: ""; display: inline-block; width: 7px; height: 7px;
    background: var(--cyan); border-radius: 50%;
    margin: 0 7px 2px 10px; vertical-align: middle;
  }
</style>
</head>
<body>
<main class="stage">
  <section class="card card--front">
    <div class="front-name">RV Bone &amp; Vitality</div>
    <div class="front-sub"><span class="front-sub__rule"></span>Center<span class="front-sub__rule"></span></div>
  </section>

  <section class="card card--back">
    <div class="back-name">RV Bone &amp;<br>Vitality<br>Center</div>
    <div class="divider"></div>

    <div class="contact">
      <p class="contact__name">Lydia Vance, M.D.</p>
      <p class="contact__title">Board Certified Hand and<br>Upper Extremity Surgeon</p>
      <p class="contact__address">38517 North Willowmere Ave<br>Maple Harbor, FL 33098</p>
      <ul class="contact__list">
        <li>
          <svg viewBox="0 0 24 24" aria-hidden="true"><path fill="none" stroke="#1cb5e0" stroke-width="2" d="M5 3l4 1 1 5-2 2a12 12 0 0 0 5 5l2-2 5 1 1 4c-1 2-3 3-5 2C10 19 5 14 3 8c-1-2 0-4 2-5z"/></svg>
          954-218-4063
        </li>
        <li>
          <svg viewBox="0 0 24 24" aria-hidden="true"><rect x="3" y="9" width="18" height="12" rx="1" fill="none" stroke="#1cb5e0" stroke-width="2"/><rect x="7" y="3" width="10" height="6" fill="none" stroke="#1cb5e0" stroke-width="2"/><path d="M7 13h2M11 13h2M15 13h2M7 17h2M11 17h2M15 17h2" stroke="#1cb5e0" stroke-width="2"/></svg>
          954-582-7341
        </li>
        <li>
          <svg viewBox="0 0 24 24" aria-hidden="true"><circle cx="12" cy="12" r="9" fill="none" stroke="#1cb5e0" stroke-width="1.8"/><ellipse cx="12" cy="12" rx="4" ry="9" fill="none" stroke="#1cb5e0" stroke-width="1.5"/><path d="M3 12h18M5 7h14M5 17h14" stroke="#1cb5e0" stroke-width="1.5"/></svg>
          www.myrvbonecare.example
        </li>
        <li>
          <svg viewBox="0 0 24 24" aria-hidden="true"><rect x="3" y="7" width="18" height="14" fill="none" stroke="#1cb5e0" stroke-width="2"/><path d="M3 8l9 7 9-7" fill="none" stroke="#1cb5e0" stroke-width="2"/></svg>
          info@myrvbonecare.example
        </li>
      </ul>
    </div>

    <p class="slogan"><span>Steady in Skill</span> <span>Centered on You</span></p>
  </section>
</main>
</body>
</html>
```